Business Card Design Project

Looking to update our business cards. We have a logo with our slogan. We are an IT firm so we wouldlike a modern look.

Industry/Entity Type

Business

```html
<!DOCTYPE html>
<html lang="en">
<head>
<meta charset="utf-8">
<title>Kelvara Tech – Business Cards</title>
<link href="https://fonts.googleapis.com/css2?family=Open+Sans:wght@400;600&display=swap" rel="stylesheet">
<style>
  :root {
    --backdrop: #dfe4e6;
    --card: #ffffff;
    --ink: #2e2e2e;
    --ink-soft: #4a4a4a;
    --rule: #555555;
    --brand-green: #7a9a3a;
    --band-lime: #b8cf2c;
  }
  * { margin: 0; padding: 0; box-sizing: border-box; }
  html, body {
    width: 1200px; height: 960px; overflow: hidden;
    background: var(--backdrop);
    font-family: "Open Sans", Arial, sans-serif;
  }
  .sheet {
    width: 1200px; height: 960px;
    display: flex; flex-direction: column;
    align-items: center; justify-content: center; gap: 56px;
  }
  .card {
    position: relative;
    width: 700px; height: 400px;
    background: var(--card);
    box-shadow: 0 4px 18px rgba(0,0,0,0.12);
    overflow: hidden;
  }
  .brand {
    display: flex; flex-direction: column; align-items: center;
  }
  .brand-name {
    display: flex; align-items: center; gap: 10px;
    color: var(--brand-green);
    font-weight: 600; letter-spacing: 0.12em;
  }
  .brand-dot {
    border-radius: 50%; background: var(--brand-green);
  }
  .brand-tagline {
    color: var(--ink-soft); font-weight: 600;
    letter-spacing: 0.22em; text-transform: uppercase;
  }

  /* Front */
  .card-front .brand { position: absolute; top: 56px; right: 46px; }
  .card-front .brand-name { font-size: 40px; }
  .card-front .brand-dot { width: 14px; height: 14px; }
  .card-front .brand-tagline { font-size: 11px; margin-top: 2px; }
  .person { position: absolute; left: 44px; top: 184px; }
  .person-name { font-size: 34px; font-weight: 400; color: var(--ink); line-height: 1.1; }
  .person-role { font-size: 17px; color: var(--ink-soft); margin-top: 4px; }
  .rule-top {
    position: absolute; left: 290px; right: 44px; top: 222px;
    border-top: 1.5px solid var(--rule);
  }
  .rule-bottom {
    position: absolute; left: 44px; right: 44px; top: 274px;
    border-top: 1.5px solid var(--rule);
  }
  .contact-list {
    position: absolute; left: 44px; top: 300px;
    list-style: none; font-size: 17px; color: var(--ink); line-height: 1.5;
  }
  .contact-list .key {
    display: inline-block; width: 38px; color: var(--brand-green);
  }
  .contact-list .accent { color: var(--brand-green); }
  .address {
    position: absolute; right: 44px; top: 296px; width: 290px;
    font-size: 15px; color: var(--ink); line-height: 1.5; font-style: normal;
  }

  /* Back */
  .card-back .brand { position: absolute; top: 116px; left: 0; right: 0; }
  .card-back .brand-name { font-size: 62px; }
  .card-back .brand-dot { width: 20px; height: 20px; }
  .card-back .brand-tagline { font-size: 16px; margin-top: 4px; }
  .web-band {
    position: absolute; left: 0; right: 0; bottom: 0; height: 46px;
  }
  .web-band svg { position: absolute; inset: 0; }
  .web-band-text {
    position: relative; display: block; text-align: center;
    line-height: 50px; font-size: 15px; font-weight: 600;
    letter-spacing: 0.08em; color: var(--ink);
  }
</style>
</head>
<body>
<main class="sheet">
  <section class="card card-front" aria-label="Business card front">
    <div class="brand">
      <div class="brand-name"><span>KELVARA TECH</span><span class="brand-dot"></span></div>
      <div class="brand-tagline">Making Technology Easy</div>
    </div>
    <div class="person">
      <h1 class="person-name">JOHN DOE</h1>
      <p class="person-role">Managing Partner</p>
    </div>
    <div class="rule-top"></div>
    <div class="rule-bottom"></div>
    <ul class="contact-list">
      <li><span class="key">t</span>(480) 555-0142</li>
      <li><span class="key">e</span>name@kelvaratech.com</li>
      <li><span class="key">w</span>www.<span class="accent">kelvaratech</span>.com</li>
    </ul>
    <address class="address">2250 W. Harlow Ave Suite 410<br>Chicago Il. 60612-3044</address>
  </section>

  <section class="card card-back" aria-label="Business card back">
    <div class="brand">
      <div class="brand-name"><span>KELVARA TECH</span><span class="brand-dot"></span></div>
      <div class="brand-tagline">Making Technology Easy</div>
    </div>
    <div class="web-band">
      <svg width="700" height="46" viewBox="0 0 700 46" aria-hidden="true">
        <path d="M170 46 L186 10 Q190 2 200 2 L500 2 Q510 2 514 10 L530 46 Z" fill="var(--band-lime)"/>
        <rect x="0" y="40" width="700" height="6" fill="var(--band-lime)"/>
      </svg>
      <span class="web-band-text">www.kelvaratech.com</span>
    </div>
  </section>
</main>
</body>
</html>
```